'Velunor' Nutritional supplements label design (UPDATED)

- 'Velunor' is a upscale health supplements brand
-The company will be packing the products in plastic bottles like other supplements
-Try to use a distinct design which is recognizable from distance
-Brand Logo is attached

-UPDATE- 2-

Label Dimensions and Design:

Hi Everyone,

Sorry for the late response caused by some very busy schedule.

Anyhow, here are the dimensions of the label (Self Adhesive) that we need:

Length of Label : 18cm
Height of Label : 6.5 cm

Product Names:

-Metabolism Formula
-Complete Multivitamins and Minerals (For Men, Women and Kids)
-Healthy Bones
-Skin Support
-Omega-3 oil for Healthy Heart

As for the ingredients just use Lorem Ipsum for now.

Many thanks to all of you in advance.

Target Market(s)

Middle Income families

Industry/Entity Type

Plastic

Requirements
Must have
• -Quality
-Effective
-Unique

```html
<!DOCTYPE html>
<html lang="en">
<head>
<meta charset="utf-8">
<title>Velunor Metabolism Formula Label</title>
<link href="https://fonts.googleapis.com/css2?family=Roboto+Condensed:wght@300;400;700&family=Roboto:wght@400;500&display=swap" rel="stylesheet">
<style>
  :root {
    --brand-blue: #1f87c8;
    --brand-teal: #1fa89a;
    --brand-green: #2e9a3a;
    --bullet-green: #27ae60;
    --text-grey: #8c8c8c;
    --dark-grey: #555555;
    --divider: #bdbdbd;
    --hatch: #eeeeee;
    --paper: #ffffff;
  }
  * { box-sizing: border-box; margin: 0; padding: 0; }
  html, body { width: 1200px; height: 433px; overflow: hidden; background: var(--paper); }
  .label { position: relative; width: 1200px; height: 433px; background: var(--paper); font-family: "Roboto Condensed", "Arial Narrow", sans-serif; }
  .band-top { position: absolute; top: 0; height: 14px; background: var(--brand-blue); }
  .band-top.left { left: 0; width: 400px; }
  .band-top.right { left: 800px; width: 400px; }
  .band-bottom { position: absolute; left: 0; bottom: 0; width: 1200px; height: 15px; background: var(--brand-blue); }
  .fold { position: absolute; top: 14px; bottom: 15px; width: 1px; background: var(--divider); }
  .fold.one { left: 400px; } .fold.two { left: 800px; }

  .heading { position: absolute; color: var(--brand-blue); font-weight: 700; font-size: 20px; line-height: 1; white-space: nowrap; }
  .copy { position: absolute; display: block; width: 262px; max-width: 262px; color: var(--text-grey); font-weight: 700; font-size: 9px; line-height: 11.4px; white-space: normal; overflow-wrap: break-word; }

  .facts { position: absolute; left: 62px; top: 137px; width: 277px; height: 273px; border: 2px solid #111; border-radius: 14px; }
  .facts .heading { left: 9px; top: 5px; }
  .facts-row { position: absolute; left: 8px; width: 257px; font-size: 9px; font-weight: 700; color: var(--text-grey); white-space: nowrap; overflow: hidden; }
  .facts-rule { position: absolute; left: 8px; width: 257px; background: var(--brand-blue); }
  .facts .copy { left: 9px; top: 127px; width: 255px; max-width: 255px; }

  .accent-tab { position: absolute; left: 401px; top: 37px; width: 70px; height: 15px; background: var(--brand-teal); }
  .brand { position: absolute; left: 400px; top: 72px; width: 400px; display: flex; justify-content: center; align-items: center; gap: 10px; }
  .brand-dot { width: 30px; height: 30px; border-radius: 50%; background: var(--brand-teal); }
  .brand-name { font-weight: 400; font-size: 34px; letter-spacing: 4px; color: var(--brand-blue); }

  .banner { position: absolute; left: 401px; top: 146px; }
  .product-name { position: absolute; left: 401px; top: 170px; width: 320px; text-align: center; color: #fff; font-weight: 700; font-size: 26px; white-space: nowrap; }
  .product-sub { position: absolute; left: 604px; top: 202px; color: #fff; font-weight: 300; font-size: 18px; }

  .benefits { position: absolute; left: 505px; top: 265px; list-style: none; font-family: "Roboto", Arial, sans-serif; font-size: 12px; color: var(--dark-grey); }
  .benefits li { height: 21px; display: flex; align-items: center; gap: 7px; }
  .benefits li::before { content: ""; width: 6px; height: 6px; background: var(--bullet-green); }

  .footer-panel { position: absolute; left: 401px; top: 350px; width: 398px; height: 55px; background: var(--hatch); }
  .daily { position: absolute; left: 401px; top: 363px; width: 398px; text-align: center; font-family: "Roboto", Arial, sans-serif; color: var(--brand-green); font-size: 12px; font-weight: 400; }
  .daily-rule { position: absolute; left: 525px; top: 379px; width: 150px; height: 2px; background: var(--brand-green); }
  .pack-info { position: absolute; left: 401px; top: 385px; width: 398px; text-align: center; font-family: "Roboto", Arial, sans-serif; font-size: 7.5px; color: var(--dark-grey); letter-spacing: .3px; }
</style>
</head>
<body>
<div class="label">
  <div class="band-top left"></div>
  <div class="band-top right"></div>
  <div class="band-bottom"></div>
  <div class="fold one"></div>
  <div class="fold two"></div>

  <h2 class="heading" style="left:72px;top:23px;">Metabolism</h2>
  <p class="copy" style="left:72px;top:47px;">The lorem ispum text is dummy text for printing and web. This is made by our official website. We can show different text according to our use .The lorem ispum text is dummy text for printing and web. This is made by our official website. We can show different text according to our use .The lorem ispum text is dummy text for printing and web. This is made by our official website. We can show different text according to our use .</p>

  <section class="facts">
    <h2 class="heading">Metabolism</h2>
    <div class="facts-rule" style="top:25px;height:4px;"></div>
    <div class="facts-row" style="top:34px;">The lorem ispum text is dummy..............................100mg</div>
    <div class="facts-rule" style="top:49px;height:3px;"></div>
    <div class="facts-row" style="top:57px;">The lorem ispum text is dummy..............................100mg</div>
    <div class="facts-rule" style="top:73px;height:3px;"></div>
    <div class="facts-row" style="top:81px;">The lorem ispum text is dummy..............................100mg</div>
    <div class="facts-rule" style="top:97px;height:3px;"></div>
    <div class="facts-row" style="top:105px;">The lorem ispum text is dummy..............................100mg</div>
    <p class="copy">The lorem ispum text is dummy text for printing and web. This is made by our official website. We can show different text according to our use .The lorem ispum text is dummy text for printing and web. This is made by our official website. We can show different text according to our use .The lorem ispum text is dummy text for printing and web. This is made by our official website. We can show different text according to our use .The lorem ispum text is dummy text for printing and web. This is made by our official website. We can show different text according to our use .The lorem ispum text is dummy text for printing and web. This is made by our official website. We can show different text according to our use .</p>
  </section>

  <div class="accent-tab"></div>
  <div class="brand"><span class="brand-dot"></span><span class="brand-name">VELUNOR</span></div>

  <svg class="banner" width="322" height="100" viewBox="0 0 322 100" aria-hidden="true">
    <path d="M0 0 H312 Q318 0 318 8 V12 H0 Z" fill="var(--brand-teal)"/>
    <path d="M0 11 H318 V72 L300 90 H0 Z" fill="var(--brand-blue)"/>
    <rect x="0" y="90" width="300" height="8" fill="var(--hatch)"/>
    <path d="M300 90 L318 72 H322 L304 98 H300 Z" fill="var(--hatch)"/>
  </svg>
  <h1 class="product-name">Metabolism Formula</h1>
  <div class="product-sub">Fat Burn</div>

  <ul class="benefits">
    <li>Healthy Energy Levels</li>
    <li>Healthy Immune System Function</li>
    <li>Healthy Maetabolism</li>
  </ul>

  <div class="footer-panel"></div>
  <div class="daily">DAILY NUTRITION</div>
  <div class="daily-rule"></div>
  <div class="pack-info">60 CAPSULES &nbsp;|&nbsp; DIETRY SUPPLEMENT</div>

  <h2 class="heading" style="left:872px;top:23px;">How to use it.</h2>
  <p class="copy" style="left:872px;top:50px;">The lorem ispum text is dummy text for printing and web. This is made by our official website. We can show different text according to our use .The lorem ispum text is dummy text for printing and web. This is made by our official website. We can show different text according to our use .The lorem ispum text is dummy text for printing and web. This is made by our official website. We can show different text according to our use .</p>
  <h2 class="heading" style="left:872px;top:157px;">Precautions</h2>
  <p class="copy" style="left:872px;top:182px;">The lorem ispum text is dummy text for printing and web. This is made by our official website. We can show different text according to our use .The lorem ispum text is dummy text for printing and web. This is made by our official website. We can show different text according to our use .The lorem ispum text is dummy text for printing and web. This is made by our official website. We can show different text according to our use .</p>
  <h2 class="heading" style="left:872px;top:291px;">Safety Temperature</h2>
  <p class="copy" style="left:872px;top:316px;">The lorem ispum text is dummy text for printing and web. This is made by our official website. We can show different text according to our use .The lorem ispum text is dummy text for printing and web. This is made by our official website. We can show different text according to our use .The lorem ispum text is dummy text for printing and web. This is made by our official website. We can show different text according to our use .</p>
</div>
</body>
</html>
```